Website Design for Wheels for Servicemen.org - Donated Cars to Disabled Vets

Need a Wordpress website. The coding now, esp. the CDONT coding is not supported by many hosting sites. Looking for a landing page to generate leads.

Logo Text

look at current one for ideas

Coding

Coded - Design and coding required

Number of Pages Required

1 page

Requirements
Must have
• look at current website at www.wheelsforservicemen.org
Nice to have
• look at this site: http://givevehicletoservicemen.org

```html
<!DOCTYPE html>
<html lang="en">
<head>
<meta charset="utf-8">
<title>Wheels for Servicemen – Donate Your Car</title>
<link rel="stylesheet" href="https://fonts.googleapis.com/css2?family=Open+Sans:wght@400;600;700&family=Oswald:wght@400;500&display=swap">
<style>
:root{
  --blue:#1f6fc4;
  --blue-dark:#12508f;
  --nav:#0e3f74;
  --red:#c8231c;
  --red-dark:#a81a14;
  --ink:#222;
  --muted:#777;
  --grey-bg:#efefef;
  --foot-bg:#f4f4f4;
  --white:#fff;
}
*{box-sizing:border-box;margin:0;padding:0}
html,body{width:706px;height:1200px;overflow:hidden}
body{position:relative;font-family:"Open Sans",Arial,sans-serif;color:var(--ink);background:var(--white)}
.abs{position:absolute}
.header{left:0;top:0;width:706px;height:62px;background:linear-gradient(180deg,#2a7ad0,#1c64b6)}
.brand{left:52px;top:16px;display:flex;align-items:center;gap:6px;color:var(--white);font-size:15px;font-weight:700}
.brand-dot{width:22px;height:22px;background:var(--red);border-radius:50%}
.contact-chip{display:flex;align-items:center;gap:8px;color:var(--white)}
.chip-icon{width:22px;height:22px;border:1.5px solid rgba(255,255,255,.8);border-radius:50%;display:flex;align-items:center;justify-content:center}
.chip-small{font-size:7.5px;line-height:1.2;opacity:.9}
.chip-big{font-size:12px;font-weight:700;line-height:1.2}
.nav{left:0;top:62px;width:706px;height:28px;background:var(--nav)}
.nav a{position:absolute;top:0;height:28px;line-height:28px;color:var(--white);font-size:9.5px;text-decoration:none;transform:translateX(-50%)}
.nav a.active{left:52px;width:90px;text-align:center;transform:none;background:#0a0f18}
.hero{left:0;top:90px;width:706px;height:303px;background:linear-gradient(100deg,#9aa3ab 0%,#5c6670 35%,#2a2f36 55%,#8c959d 100%)}
.hero-title{left:51px;top:276px;font-family:"Oswald",Arial,sans-serif;font-size:19px;line-height:24px;color:var(--white);text-shadow:0 1px 3px rgba(0,0,0,.5)}
.slider-btn{top:337px;width:14px;height:14px;border-radius:50%;background:rgba(40,40,40,.7);display:flex;align-items:center;justify-content:center}
.form-box{left:435px;top:126px;width:219px;height:248px;background:var(--red)}
.form-head{left:0;top:0;width:219px;height:60px}
.form-head p{position:absolute;width:100%;text-align:center;color:var(--white)}
.form-title{left:0;top:68px;width:219px;text-align:center;color:var(--white);font-size:13px}
.field{width:89px;height:21px;background:var(--white);border-radius:2px;font-size:7px;color:#555;padding-left:6px;line-height:21px}
.btn-donate{left:66px;top:212px;width:89px;height:22px;background:var(--blue);border-radius:2px;color:var(--white);font-size:9px;text-align:center;line-height:22px}
.section-title{left:0;width:706px;text-align:center;color:var(--red);font-size:14.5px;font-weight:600}
.step-icon{width:55px;height:55px;background:var(--blue);border-radius:2px;display:flex;align-items:center;justify-content:center;box-shadow:0 2px 3px rgba(0,0,0,.2)}
.step-title{font-size:10px;color:#333}
.step-text{font-size:7px;line-height:12px;color:var(--muted);width:117px;text-align:justify}
.why{left:0;top:572px;width:706px;height:238px;background:var(--grey-bg)}
.why-title{left:51px;top:36px;font-size:13px;font-weight:600}
.why-text{left:51px;top:60px;width:265px;font-size:7.2px;line-height:11.5px;color:#555}
.why-text p{margin-bottom:3px}
.read-more{left:52px;top:188px;width:66px;height:19px;border:1px solid var(--red);border-radius:10px;color:var(--red);font-size:7px;text-align:center;line-height:17px;background:var(--white)}
.video{left:350px;top:28px;width:300px;height:177px;background:var(--white);padding:3px;box-shadow:0 0 2px rgba(0,0,0,.3)}
.video-media{width:100%;height:100%;background:linear-gradient(110deg,#c9cdd1,#8f969c 45%,#c79a7a 70%,#a3796a);display:flex;align-items:center;justify-content:center}
.play{width:40px;height:40px;border-radius:50%;background:rgba(20,20,20,.75);display:flex;align-items:center;justify-content:center}
.prog{width:64px;height:64px;border-radius:50%;background:var(--white);box-shadow:0 0 0 1px #e2e2e2,0 1px 4px rgba(0,0,0,.15);display:flex;align-items:center;justify-content:center;transform:translate(-50%,-50%)}
.prog-label{width:140px;text-align:center;font-size:9.5px;line-height:14px;color:#333;transform:translateX(-50%)}
.footer{left:0;top:1023px;width:706px;height:177px;background:var(--foot-bg)}
.foot-h{font-size:8.5px;color:#333;top:38px}
.foot-small{font-size:6.5px;line-height:12.5px;color:#666}
.badge{width:30px;height:24px;border-radius:50%;background:#8fb6d6}
.badge-rect{width:54px;height:18px;background:#c9c9c9;border-radius:2px}
.email-in{width:87px;height:18px;border:1px solid #ccc;background:var(--white);font-size:6.5px;color:#777;padding-left:5px;line-height:16px}
.btn-submit{width:33px;height:18px;background:var(--red-dark);color:var(--white);font-size:6.5px;text-align:center;line-height:18px}
.social{width:14px;height:14px;background:#555;border-radius:2px}
.foot-line{left:54px;top:130px;width:603px;height:1px;background:#d4d4d4}
.copy{left:0;top:146px;width:706px;text-align:center;font-size:7px;color:#333}
</style>
</head>
<body>

<header class="abs header">
  <div class="abs brand"><span class="brand-dot"></span>Wheels for Servicemen</div>
  <div class="abs contact-chip" style="left:376px;top:18px">
    <div class="chip-icon"><svg width="11" height="11" viewBox="0 0 12 12"><circle cx="6" cy="6" r="4.5" fill="none" stroke="#fff" stroke-width="1.3"/><path d="M6 3.5V6h2" fill="none" stroke="#fff" stroke-width="1.3"/></svg></div>
    <div><div class="chip-small">LIVE OPERATORS AVAILABLE</div><div class="chip-big">7DAYS A WEEK</div></div>
  </div>
  <div class="abs contact-chip" style="left:526px;top:18px">
    <div class="chip-icon"><svg width="11" height="11" viewBox="0 0 24 24"><path fill="#fff" d="M6.6 10.8a15 15 0 006.6 6.6l2.2-2.2c.3-.3.7-.4 1-.2 1.1.4 2.3.6 3.6.6.6 0 1 .4 1 1V20c0 .6-.4 1-1 1A17 17 0 013 4c0-.6.4-1 1-1h3.5c.6 0 1 .4 1 1 0 1.3.2 2.5.6 3.6.1.3 0 .7-.2 1z"/></svg></div>
    <div><div class="chip-small" style="font-size:9px">WE NEED YOUR HELP</div><div class="chip-big" style="font-size:10.5px">Call 1-800-555-0142</div></div>
  </div>
</header>

<nav class="abs nav">
  <a class="active" href="#">HOME</a>
  <a href="#" style="left:194px">HOW IT WORKS</a>
  <a href="#" style="left:303px">CHARITIES</a>
  <a href="#" style="left:412px">TAX DEDUCTION</a>
  <a href="#" style="left:508px">FAQ</a>
  <a href="#" style="left:595px">CONTACT US</a>
</nav>

<section class="abs hero" role="img" aria-label="Smiling man holding out car keys in front of a dark car"></section>
<h1 class="abs hero-title" style="font-weight:400">DONATE YOUR CAR : FULL TAX DEDUCTION<br>- RUNNING OR NOT</h1>
<div class="abs slider-btn" style="left:53px"><svg width="6" height="6" viewBox="0 0 6 6"><path d="M4 1L2 3l2 2" fill="none" stroke="#fff" stroke-width="1"/></svg></div>
<div class="abs slider-btn" style="left:71px"><svg width="6" height="6" viewBox="0 0 6 6"><path d="M2 1l2 2-2 2" fill="none" stroke="#fff" stroke-width="1"/></svg></div>

<form class="abs form-box">
  <div class="abs form-head">
    <svg class="abs" style="left:0;top:0" width="219" height="60" viewBox="0 0 219 60"><path d="M0 0H219V38L109.5 60 0 38Z" fill="var(--red-dark)"/></svg>
    <p style="top:12px;font-size:7.5px">PLEASE FILL OUT FORM OR</p>
    <p style="top:23px;font-size:10px;font-weight:600">Call toll - Free 1-800-555-0142</p>
  </div>
  <div class="abs form-title">DONATE HERE</div>
  <div class="abs field" style="left:15px;top:96px">Name</div>
  <div class="abs field" style="left:115px;top:96px">Email</div>
  <div class="abs field" style="left:15px;top:124px">Phone Number</div>
  <div class="abs field" style="left:115px;top:124px">Cell Phone</div>
  <div class="abs field" style="left:15px;top:151px">Address</div>
  <div class="abs field" style="left:115px;top:151px">City</div>
  <div class="abs field" style="left:15px;top:178px">State</div>
  <div class="abs field" style="left:115px;top:178px">Zip Code</div>
  <div class="abs btn-donate">Donate Now</div>
</form>

<h2 class="abs section-title" style="top:420px">HOW IT WORKS</h2>

<div class="abs step-icon" style="left:51px;top:467px"><svg width="20" height="20" viewBox="0 0 24 24"><rect x="2" y="2" width="20" height="20" rx="4" fill="#fff"/><path fill="var(--blue)" d="M8 6.5c.4 0 .8.3.9.7l.5 2c.1.3 0 .6-.3.8l-1 .8a8 8 0 004.1 4.1l.8-1c.2-.3.5-.4.8-.3l2 .5c.4.1.7.5.7.9v1.5c0 .6-.4 1-1 1A11 11 0 016.5 7.5c0-.6.4-1 1-1z"/></svg></div>
<div class="abs step-title" style="left:118px;top:468px">CALL US</div>
<p class="abs step-text" style="left:118px;top:484px">Lorem Ipsum has been the industry's standard dummy text ever since the 1500s, when an un-</p>

<div class="abs step-icon" style="left:259px;top:467px"><svg width="22" height="18" viewBox="0 0 24 18"><path fill="#fff" d="M2 3h12v10H2zM14 6h4l4 4v3h-8z"/><circle cx="6" cy="14" r="2.2" fill="#fff" stroke="var(--blue)"/><circle cx="18" cy="14" r="2.2" fill="#fff" stroke="var(--blue)"/></svg></div>
<div class="abs step-title" style="left:324px;top:468px">WE TOW IT</div>
<p class="abs step-text" style="left:324px;top:487px">Lorem Ipsum has been the industry's standard dummy text ever since the 1500s, when an unknown printer</p>

<div class="abs step-icon" style="left:470px;top:467px"><svg width="18" height="22" viewBox="0 0 18 22"><path fill="#fff" d="M1 1h11l5 5v15H1z"/><path d="M4 10h10M4 13h10M4 16h10" stroke="var(--blue)" stroke-width="1.4"/></svg></div>
<div class="abs step-title" style="left:535px;top:468px">TAX WRITE-OFF</div>
<p class="abs step-text" style="left:535px;top:484px">Lorem Ipsum has been the industry's standard dummy text ever since the 1500s, when an unknown</p>

<section class="abs why">
  <h2 class="abs why-title">WHY DONATE YOUR CAR TO US?</h2>
  <div class="abs why-text">
    <p>IRS 501(c)3 Approved: Free 24/7 Pickup with No DMV Hassles.</p>
    <p>Free Local Towing to You: We will pick up your car donation, running or not, when it's most convenient, at home or work.</p>
    <p>All Cars Accepted: We take your car regardless of its condition or registration status.</p>
    <p>Income Tax Deduction: We issue you an IRS tax receipt &amp; offer the largest resale network to get you the highest tax write-off possible.</p>
    <p>No Paperwork Hassles: We take any car and handle everything: DMV, Smog and IRS paperwork.</p>
  </div>
  <div class="abs read-more">Read More »</div>
  <div class="abs video">
    <div class="video-media" role="img" aria-label="Video still of a smiling woman in a car holding up keys">
      <div class="play"><svg width="16" height="18" viewBox="0 0 16 18"><path d="M2 1l13 8-13 8z" fill="#fff"/></svg></div>
    </div>
  </div>
</section>

<h2 class="abs section-title" style="top:844px">CAR DONATION PROGRAM</h2>

<div class="abs prog" style="left:130px;top:928px"><svg width="34" height="20" viewBox="0 0 34 20"><path d="M2 4l8-2 14 1 8-1-1 6-4 4-2 6-3-3-8 0-5-2-5-3z" fill="#5a7fbf"/></svg></div>
<div class="abs prog" style="left:282px;top:928px"><svg width="24" height="18" viewBox="0 0 24 18"><path d="M5 3h14l3 6v7h-3v-2H5v2H2V9z" fill="#5a7fbf"/><rect x="6" y="4.5" width="12" height="4" fill="#fff"/><circle cx="6" cy="11" r="1.4" fill="#fff"/><circle cx="18" cy="11" r="1.4" fill="#fff"/></svg></div>
<div class="abs prog" style="left:434px;top:928px"><svg width="18" height="22" viewBox="0 0 18 22"><path d="M1 1h11l5 5v15H1z" fill="none" stroke="#5a7fbf" stroke-width="1.3"/><path d="M4 10h10M4 13h10M4 16h10" stroke="#5a7fbf" stroke-width="1.2"/></svg></div>
<div class="abs prog" style="left:587px;top:928px"><svg width="32" height="20" viewBox="0 0 32 20"><path d="M2 2l8 10" stroke="#5a7fbf" stroke-width="1.5"/><path d="M8 9h10V5h6l5 5v4H8z" fill="#5a7fbf"/><circle cx="12" cy="15" r="2.5" fill="#fff" stroke="#5a7fbf" stroke-width="1.3"/><circle cx="25" cy="15" r="2.5" fill="#fff" stroke="#5a7fbf" stroke-width="1.3"/></svg></div>

<div class="abs prog-label" style="left:130px;top:966px">DONATIONS ACCEPTED<br>NATIONWIDE</div>
<div class="abs prog-label" style="left:282px;top:966px">ALL VECHICLE<br>TYPES WELCOME</div>
<div class="abs prog-label" style="left:434px;top:973px">TAX DEDUCTIBLE</div>
<div class="abs prog-label" style="left:587px;top:973px">TOWING FREE</div>

<footer class="abs footer">
  <div class="abs foot-h" style="left:52px">SAFE &amp; SECURE</div>
  <div class="abs badge" style="left:52px;top:80px"></div>
  <div class="abs badge-rect" style="left:97px;top:83px"></div>

  <div class="abs foot-h" style="left:212px">CONTACT US</div>
  <div class="abs foot-small" style="left:213px;top:58px">Address : 12 Harbor Lane, Old Quay<br>Dunmore, DN4 2KL<br>Phone : +971 4 555 0199<br>Email : info@examplemail.com</div>

  <div class="abs foot-h" style="left:374px">JOIN OUR MAILING LIST</div>
  <div class="abs foot-small" style="left:374px;top:58px;line-height:10px;width:110px">Your about us information would fit here nicely.</div>
  <div class="abs email-in" style="left:374px;top:78px">Email address</div>
  <div class="abs btn-submit" style="left:460px;top:78px">Submit</div>

  <div class="abs foot-h" style="left:554px">FOLLOW US OUT THERE</div>
  <div class="abs social" style="left:554px;top:59px"></div>
  <div class="abs social" style="left:576px;top:59px"></div>
  <div class="abs social" style="left:599px;top:59px"></div>
  <div class="abs social" style="left:622px;top:59px"></div>

  <div class="abs foot-line"></div>
  <div class="abs copy">Copyright © 2016. All Rights Reserved</div>
</footer>

</body>
</html>
```